RB Halden Electric Yard Sign

Looking to have a yard sign designed that we can place at projects we are working on. Most likely will be 18" H x 24" W but flexible that we can increase the size if necessary. It should include our logo, our phone # 609-555-0147, website rbhaldenelectric.example and slogan, built on integrity, driven by excellence. Colors should match our brand.

```html
<!DOCTYPE html>
<html lang="en">
<head>
<meta charset="utf-8">
<title>RB Halden Electric Yard Sign</title>
<link rel="stylesheet" href="https://fonts.googleapis.com/css2?family=Bebas+Neue&family=Barlow+Condensed:ital,wght@1,600&display=swap">
<style>
  :root {
    --backdrop: #4b4b4b;
    --sign-white: #ffffff;
    --brand-navy: #0f3a5f;
    --brand-red: #e3202b;
    --text-light: #ffffff;
  }
  html, body {
    margin: 0;
    padding: 0;
    width: 1200px;
    height: 1001px;
    overflow: hidden;
    background: var(--backdrop);
  }
  .yard-sign {
    position: absolute;
    left: 120px;
    top: 140px;
    width: 960px;
    height: 720px;
    display: flex;
    flex-direction: column;
    box-shadow: 0 10px 30px rgba(0,0,0,0.35);
  }
  .brand-panel {
    height: 306px;
    background: var(--sign-white);
    display: flex;
    align-items: center;
    justify-content: center;
  }
  .brand-name {
    font-family: "Bebas Neue", sans-serif;
    font-size: 92px;
    letter-spacing: 4px;
    color: var(--brand-red);
    line-height: 1;
    padding-top: 40px;
  }
  .contact-panel {
    height: 294px;
    background: var(--brand-navy);
    display: flex;
    flex-direction: column;
    justify-content: center;
    align-items: center;
    gap: 6px;
  }
  .contact-line {
    display: flex;
    align-items: center;
    gap: 18px;
    color: var(--text-light);
    font-family: "Bebas Neue", sans-serif;
    line-height: 0.9;
  }
  .contact-line svg { flex: none; }
  .phone-number { font-size: 160px; }
  .web-address { font-size: 74px; letter-spacing: 1px; }
  .slogan-band {
    height: 120px;
    background: var(--brand-red);
    display: flex;
    align-items: center;
    justify-content: center;
  }
  .slogan {
    font-family: "Barlow Condensed", sans-serif;
    font-style: italic;
    font-weight: 600;
    font-size: 54px;
    color: var(--text-light);
    text-transform: uppercase;
    letter-spacing: 0.5px;
  }
</style>
</head>
<body>
  <div class="yard-sign">
    <div class="brand-panel">
      <div class="brand-name">RB Halden Electric</div>
    </div>
    <div class="contact-panel">
      <div class="contact-line">
        <svg width="34" height="44" viewBox="0 0 24 32" aria-hidden="true">
          <path d="M7 2 C4 3 2 6 3 12 C4 19 9 27 14 30 C17 31 19 30 20 28 L21 25 L16 21 L13 23 C10 20 8 15 8 11 L11 9 L9 2 Z" fill="var(--brand-red)"/>
        </svg>
        <span class="phone-number">609-555-0147</span>
      </div>
      <div class="contact-line">
        <svg width="40" height="40" viewBox="0 0 24 24" aria-hidden="true">
          <circle cx="12" cy="12" r="10" fill="none" stroke="var(--brand-red)" stroke-width="2.2"/>
          <ellipse cx="12" cy="12" rx="4.5" ry="10" fill="none" stroke="var(--brand-red)" stroke-width="2"/>
          <line x1="2" y1="12" x2="22" y2="12" stroke="var(--brand-red)" stroke-width="2"/>
          <line x1="4" y1="7" x2="20" y2="7" stroke="var(--brand-red)" stroke-width="1.6"/>
          <line x1="4" y1="17" x2="20" y2="17" stroke="var(--brand-red)" stroke-width="1.6"/>
        </svg>
        <span class="web-address">RBHALDENELECTRIC.EXAMPLE</span>
      </div>
    </div>
    <div class="slogan-band">
      <span class="slogan">Built on integrity, driven by excellence</span>
    </div>
  </div>
</body>
</html>
```